KRV Photography Business Card Design

I would like a business card designed in the shape of a camera.
Would like to see various camera designs. Would like to see what the card looks like in different colors. Would like to see which logo looks better on the various camera designs so please show me some with the white logo and some with the black logo. If you need a different file formats please let me know.
Project Deadline Extended Reason: My grandfather passed away and dealing with funeral plans so need to extend deadline. Added Tuesday, March 1, 2016
Project Deadline Extended
Reason: I just got back from out of town. My grandfather's passing was the primary focus for me these past few weeks and the funeral is over so now I will concentrate on picking my business card design. I really appreciate each designer who has taken the time to submit a design. Your effort has not gone unnoticed. I look forward to seeing more amazing designs.
Business
Contact Information for Business Card
Dorine
555-418-2706
https://www.facebook.com/krvphotographyfreelance/
MonaDorine@krv-photography.example

```html
<!DOCTYPE html>
<html lang="en">
<head>
<meta charset="utf-8">
<title>KRV Photography – Business Card</title>
<link rel="stylesheet" href="https://fonts.googleapis.com/css2?family=Cinzel:wght@400&family=Mulish:wght@500&display=swap">
<style>
  :root {
    --page: #ffffff;
    --gold-light: #f6e27a;
    --gold: #ecce2a;
    --gold-deep: #e2c210;
    --gold-edge: #a99620;
    --gold-shine: #f4f1d8;
    --ink: #000000;
    --text-dark: #1f1f1f;
    --brand-gold: #e3c46c;
  }
  html, body {
    margin: 0;
    width: 1200px;
    height: 802px;
    overflow: hidden;
    background: var(--page);
  }
  .card {
    display: block;
    width: 1200px;
    height: 802px;
  }
  .brand-line {
    font-family: "Cinzel", serif;
    font-size: 27px;
    letter-spacing: 0.5px;
    fill: var(--brand-gold);
  }
  .holder-name {
    font-family: "Mulish", sans-serif;
    font-weight: 500;
    font-size: 42px;
    fill: var(--text-dark);
  }
  .phone-number {
    font-family: "Mulish", sans-serif;
    font-weight: 500;
    font-size: 35px;
    fill: var(--text-dark);
  }
  .lens-name {
    font-family: "Cinzel", serif;
    font-weight: 400;
    font-size: 60px;
    fill: var(--brand-gold);
  }
</style>
</head>
<body>
<svg class="card" viewBox="0 0 1132 756" preserveAspectRatio="xMidYMid meet" role="img" aria-label="KRV Photography camera-shaped business card">
  <defs>
    <linearGradient id="body-fill" x1="0" y1="0" x2="0" y2="1">
      <stop offset="0" stop-color="var(--gold-light)"/>
      <stop offset="1" stop-color="var(--gold-deep)"/>
    </linearGradient>
  </defs>

  <g class="camera-outline" fill="var(--gold-edge)" stroke="var(--gold-edge)" stroke-width="16">
    <rect x="185" y="88" width="125" height="80" rx="35"/>
    <rect x="335" y="30" width="430" height="140" rx="50"/>
    <rect x="36" y="128" width="1058" height="496" rx="90"/>
    <ellipse cx="735" cy="470" rx="303" ry="250"/>
  </g>
  <g class="camera-body" fill="url(#body-fill)">
    <rect x="185" y="88" width="125" height="80" rx="35"/>
    <rect x="335" y="30" width="430" height="140" rx="50"/>
    <rect x="36" y="128" width="1058" height="496" rx="90"/>
    <ellipse cx="735" cy="470" rx="303" ry="250"/>
  </g>

  <path class="top-band" fill="var(--ink)" stroke="var(--gold-shine)" stroke-width="4"
        d="M80,338 L80,215 Q80,165 130,165 L385,165 L385,95 Q385,68 415,68 L688,68 Q715,68 715,95 L715,165 L995,165 Q1050,165 1050,220 L1050,335 Q960,300 880,270 L420,270 Q380,285 380,300 Q220,290 80,338 Z"/>

  <rect class="viewfinder" x="462" y="108" width="175" height="52" rx="26" fill="var(--gold-light)" stroke="var(--gold-shine)" stroke-width="5"/>

  <g class="lens">
    <ellipse cx="735" cy="470" rx="290" ry="240" fill="var(--gold)" stroke="var(--gold-shine)" stroke-width="5"/>
    <path d="M470,240 Q380,300 385,400 Q390,470 410,495 Q395,400 440,320 Q490,250 600,225 Q530,222 470,240 Z" fill="var(--ink)" stroke="var(--gold-shine)" stroke-width="4"/>
    <ellipse cx="730" cy="462" rx="268" ry="222" fill="var(--ink)" stroke="var(--gold-shine)" stroke-width="4"/>
    <ellipse cx="737" cy="475" rx="240" ry="196" fill="none" stroke="var(--gold)" stroke-width="16"/>
    <ellipse cx="737" cy="475" rx="248" ry="204" fill="none" stroke="var(--gold-shine)" stroke-width="3"/>
    <ellipse cx="730" cy="455" rx="222" ry="176" fill="var(--ink)" stroke="var(--gold-shine)" stroke-width="3"/>
  </g>

  <text class="lens-name" x="740" y="462" text-anchor="middle">KRV</text>

  <text class="brand-line" x="113" y="245">KRV PHOTOGRAPHY</text>
  <text class="holder-name" x="95" y="418">Mona</text>
  <text class="holder-name" x="95" y="478">Dorine</text>

  <g class="phone-line">
    <path class="phone-icon" fill="var(--text-dark)" transform="translate(100 540) scale(1.7)"
          d="M6.6 10.8c1.4 2.8 3.8 5.1 6.6 6.6l2.2-2.2c.3-.3.7-.4 1-.2 1.1.4 2.3.6 3.6.6.6 0 1 .4 1 1V20c0 .6-.4 1-1 1C10.6 21 3 13.4 3 4c0-.6.4-1 1-1h3.5c.6 0 1 .4 1 1 0 1.3.2 2.5.6 3.6.1.3 0 .7-.2 1L6.6 10.8z"/>
    <text class="phone-number" x="158" y="577">555-418-2706</text>
  </g>
</svg>
</body>
</html>
```